Travel Agency Website - Simple General

Need a 7 page simple design that is pretty repetitive. Need to be able to load quickly that is SEO optimized. Trying to give ideas on what they can do, be personal as we are local, but at the same time come across as professional and get information easily with little burden.

- Landing Page
- Brimwell Vacations Page
- Family Trips
- Road Trips from Texas
- Other Destinations
- About Us Page
- Contact Us Page

Target Market(s)

Families

Coding

Coded - Design and coding required

Number of Pages Required

5+ page

Colors

Designer to choose colors to be used in the design.

Requirements
Must have
• Like it to flow easily with our logo. Use that for colors, etc.

```html
<!DOCTYPE html>
<html lang="en">
<head>
<meta charset="utf-8">
<title>Roamwell Travel – Plan your kind of trip</title>
<link href="https://fonts.googleapis.com/css2?family=Playfair+Display:wght@600;700&family=Lato:wght@400;700&display=swap" rel="stylesheet">
<style>
:root{
  --ink:#1f2a2a;
  --muted:#5b6665;
  --teal:#4f8f89;
  --teal-contact:#468781;
  --teal-deep:#2f6e68;
  --footer:#2d6d68;
  --mint:#e4f1f0;
  --chip:#cfe4e1;
  --white:#ffffff;
  --line:#dfe6e5;
  --star:#3f8a83;
}
*{box-sizing:border-box;margin:0;padding:0}
html,body{width:1200px;height:3769px;overflow:hidden}
body{position:relative;font-family:'Lato',sans-serif;color:var(--ink);background:var(--white)}
.serif{font-family:'Playfair Display',serif}
.abs{position:absolute}
.btn{display:inline-flex;align-items:center;justify-content:center;border-radius:20px;font-weight:700;font-size:13px;white-space:nowrap}
.btn-light{background:var(--white);color:var(--ink)}
.btn-outline{background:var(--white);border:1px solid #9aa5a4;color:var(--ink)}
.btn-dark{background:var(--teal-deep);color:var(--white)}

/* header */
.site-header{left:0;top:0;width:1200px;height:102px;background:var(--white);border-bottom:1px solid var(--line)}
.brand{left:161px;top:18px;display:flex;align-items:center;gap:8px;font-family:'Lato',sans-serif;font-weight:700;font-size:13px;color:var(--teal-deep)}
.brand .mark{width:66px;height:66px;border-radius:50%;background:var(--mint);display:flex;align-items:center;justify-content:center;text-align:center;line-height:1.1;font-size:11px}
.nav{left:273px;top:42px;display:flex;gap:25px;font-size:13px}
.nav .active{text-decoration:underline;text-underline-offset:4px}
.header-cta{left:913px;top:33px;width:126px;height:36px}

/* hero */
.hero{left:0;top:102px;width:1200px;height:413px}
.hero-photo{position:absolute;inset:0;background:linear-gradient(90deg,#6f5b48 0%,#8d7864 35%,#a99179 60%,#7d6a58 100%)}
.hero-photo::after{content:"";position:absolute;inset:0;background:linear-gradient(180deg,rgba(150,120,90,.2),rgba(70,60,55,.45))}
.hero-copy{left:161px;top:102px;width:490px;color:var(--white)}
.eyebrow{display:flex;align-items:center;gap:8px;font-size:12px;letter-spacing:.5px;text-transform:uppercase}
.hero h1{font-size:46px;font-weight:700;margin:12px 0 12px;line-height:1.15}
.hero p{font-size:13.5px;line-height:1.4;opacity:.95;width:470px}
.hero .btn{margin-top:20px;width:143px;height:38px}

/* section headings */
.sec-title{font-size:31px;font-weight:700}
.sec-sub{font-size:12px;color:var(--muted);margin-top:8px}

/* destinations */
.dest-card{width:428px;height:201px;border-radius:2px;overflow:hidden}
.dest-card .fill{position:absolute;inset:0}
.dest-card .label{position:absolute;left:12px;bottom:14px;color:var(--white);font-size:17px;font-weight:700}
.dest-card .go{position:absolute;right:12px;bottom:10px;width:32px;height:32px;border-radius:50%;background:var(--white);display:flex;align-items:center;justify-content:center}
.dest-card .rating{position:absolute;left:9px;top:24px;color:var(--white);font-size:11px}

/* about */
.about-box{left:161px;top:1226px;width:675px;height:382px;background:var(--teal)}
.about-text{left:191px;top:1257px;width:367px;color:#eef6f5;font-size:12.3px;line-height:22.5px}
.about-text .btn{margin-top:14px;width:96px;height:29px;font-size:11px}
.about-photo{left:583px;top:1262px;width:457px;height:310px;background:linear-gradient(135deg,#b9bfc4,#8e969c 50%,#4a4e55);box-shadow:0 20px 40px rgba(0,0,0,.15)}

/* activities */
.act-card{width:203px}
.act-card .img{height:202px;border-radius:2px;position:relative}
.act-card .heart{position:absolute;right:10px;top:10px;width:28px;height:28px;border-radius:50%;background:var(--white);display:flex;align-items:center;justify-content:center}
.act-card .row{display:flex;justify-content:space-between;margin-top:13px;font-size:13.5px}
.act-card .score{color:var(--star);font-size:12px;display:flex;align-items:center;gap:5px}
.act-card .desc{font-size:12px;color:var(--muted);margin-top:6px}
.carousel-next{left:1032px;top:1859px;width:33px;height:33px;border-radius:50%;background:var(--white);border:1px solid #555;display:flex;align-items:center;justify-content:center}

/* posts */
.post{left:161px;width:878px;height:133px;background:var(--mint)}
.post .thumb{position:absolute;left:18px;top:18px;width:144px;height:97px}
.post .body{position:absolute;left:189px;top:18px;width:560px}
.post .tag{display:inline-block;background:var(--chip);font-size:9.5px;padding:4px 6px;color:var(--muted)}
.post h3{font-size:17px;font-weight:700;margin:9px 0 6px}
.post p{font-size:12px;line-height:1.5;color:var(--muted)}
.post .btn{position:absolute;right:18px;bottom:18px;width:86px;height:26px;font-size:11px}

/* contact */
.contact{left:161px;top:2411px;width:878px;height:404px;background:var(--teal-contact)}
.contact-info{position:absolute;left:0;top:36px;width:208px;text-align:center;color:#e6f1f0}
.contact-info .item{margin-bottom:26px}
.contact-info h4{font-size:13px;font-weight:700;margin:8px 0 6px;color:var(--white)}
.contact-info p{font-size:10px;line-height:1.5}
.contact-info a{color:#e6f1f0;text-decoration:underline}
.contact-divider{position:absolute;left:208px;top:80px;width:1px;height:250px;background:rgba(255,255,255,.4)}
.contact-form{position:absolute;left:266px;top:32px;width:557px;color:var(--white)}
.contact-form h2{font-size:31px;font-weight:700}
.contact-form p{font-size:12px;line-height:1.5;margin:8px 0 18px;color:#e4efee}
.field{background:#f6f7f7;border:1px solid #cfd6d5;height:35px;margin-bottom:19px;font-size:10.5px;color:#8a9392;padding:11px 9px}
.field.tall{height:84px}
.contact-form .btn{width:92px;height:30px;font-size:11px;margin-top:2px}

/* promo */
.promo{left:161px;top:2875px;width:874px;height:272px;background:#e6f3f2;border:1px solid #d4e4e3;overflow:hidden}
.promo-copy{position:absolute;left:62px;top:50px;width:380px}
.promo-copy h2{font-size:31px;font-weight:600}
.promo-copy p{font-size:12px;color:var(--muted);line-height:1.35;margin-top:10px}
.promo-copy .btn{margin-top:18px;width:116px;height:32px;font-size:12px}
.promo-collage{position:absolute;left:480px;top:-40px;width:420px;height:360px}

/* footer */
.site-footer{left:0;top:3209px;width:1200px;height:560px;background:var(--footer);color:#e5efee}
.nl-eyebrow{left:190px;top:64px;font-size:12px;letter-spacing:.5px;display:flex;gap:6px;align-items:center;text-transform:uppercase}
.nl-title{left:190px;top:86px;font-size:31px;font-weight:700;color:var(--white)}
.nl-label{top:148px;font-size:11px}
.nl-input{top:164px;width:255px;height:35px;background:#f5f6f6;color:#8a9392;font-size:11px;padding:11px 18px;display:flex;justify-content:space-between}
.nl-btn{left:742px;top:164px;width:90px;height:35px;font-size:12px}
.nl-note{left:190px;top:224px;font-size:12px}
.nl-note u{text-underline-offset:3px}
.f-rule{left:161px;width:878px;height:1px;background:rgba(255,255,255,.2)}
.f-brand{left:161px;top:330px;width:140px;height:120px;display:flex;align-items:center;gap:8px;color:var(--white);font-weight:700;font-size:16px}
.f-brand .mark{width:22px;height:22px;border-radius:50%;background:var(--white)}
.f-col{top:336px;font-size:11px;line-height:20px}
.f-col h5{font-family:'Playfair Display',serif;font-size:13px;font-weight:600;margin-bottom:8px;color:var(--white)}
.socials{left:835px;top:380px;display:flex;gap:20px}
.socials span{width:33px;height:33px;border:1px solid rgba(255,255,255,.5);border-radius:4px;display:flex;align-items:center;justify-content:center}
.socials span i{width:11px;height:11px;background:rgba(255,255,255,.8);border-radius:2px}
.copyright{left:161px;top:522px;font-size:11px}
.legal{left:840px;top:522px;font-size:11px;display:flex;gap:18px}
</style>
</head>
<body>

<header class="site-header abs">
  <div class="brand abs"><div class="mark">Roamwell<br>Travel</div></div>
  <nav class="nav abs">
    <span class="active">Home</span>
    <span>Travel ⌄</span>
    <span>Brimwell Vacations</span>
    <span>Family Trips</span>
    <span>Texas Road Trips</span>
    <span>About</span>
    <span>Contact</span>
  </nav>
  <span class="btn btn-dark header-cta abs">Book your trip</span>
</header>

<section class="hero abs">
  <div class="hero-photo" role="img" aria-label="Family running hand in hand through shallow waves on a beach at sunset"></div>
  <div class="hero-copy abs">
    <div class="eyebrow">
      <svg width="14" height="14" viewBox="0 0 24 24" fill="#fff"><path d="M21 16v-2l-8-5V3.5a1.5 1.5 0 0 0-3 0V9l-8 5v2l8-2.5V19l-2 1.5V22l3.5-1 3.5 1v-1.5L13 19v-5.5z"/></svg>
      Plan your next trip
    </div>
    <h1 class="serif">Plan your kind of trip</h1>
    <p>Lorem Ipsum Dolor Sit Amet, Consectetur Adipiscing Elit, Sed Do Eiusmod Tempor Incididunt Ut Labore Et Dolore Magna Aliqua. Ut Enim Ad Minim Veniam,</p>
    <span class="btn btn-light">Book your trip</span>
  </div>
</section>

<section class="abs" style="left:161px;top:578px">
  <h2 class="sec-title serif">Popular Destinations</h2>
  <p class="sec-sub">Lorem Ipsum Dolor Sit Amet, Consectetur Adipiscing Elit, Sed Do Eiusmod Tempor</p>
</section>

<a class="dest-card abs" style="left:161px;top:658px">
  <div class="fill" role="img" aria-label="Costumed performer greeting children in front of a fairytale castle" style="background:linear-gradient(160deg,#7ea6cf,#4f6f9a 45%,#2f3a4a)"></div>
  <span class="label">Brimwell Vacations</span>
  <span class="go"><svg width="14" height="14" viewBox="0 0 24 24" fill="none" stroke="#1f2a2a" stroke-width="2.2"><path d="M4 12h15M13 6l6 6-6 6"/></svg></span>
</a>
<a class="dest-card abs" style="left:611px;top:658px">
  <div class="fill" role="img" aria-label="Family pulling suitcases along an airport walkway" style="background:linear-gradient(160deg,#d8dee0,#a9b3b5 50%,#5d5f5a)"></div>
  <span class="label">Family Trips</span>
  <span class="go"><svg width="14" height="14" viewBox="0 0 24 24" fill="none" stroke="#1f2a2a" stroke-width="2.2"><path d="M4 12h15M13 6l6 6-6 6"/></svg></span>
</a>
<a class="dest-card abs" style="left:161px;top:882px">
  <div class="fill" role="img" aria-label="Couple with a dog sitting on a pickup truck in a forest" style="background:linear-gradient(160deg,#b39a6e,#6e6a45 50%,#3a3a2c)"></div>
  <span class="label">Texas Road Trips</span>
  <span class="go"><svg width="14" height="14" viewBox="0 0 24 24" fill="none" stroke="#1f2a2a" stroke-width="2.2"><path d="M4 12h15M13 6l6 6-6 6"/></svg></span>
</a>
<a class="dest-card abs" style="left:611px;top:882px">
  <div class="fill" role="img" aria-label="Infinity pool overlooking a tropical beach" style="background:linear-gradient(180deg,#cfe0e6,#8fbfc4 45%,#3f7f86)"></div>
  <span class="rating">5.0 ★</span>
  <span class="label">Other Destinations</span>
  <span class="go"><svg width="14" height="14" viewBox="0 0 24 24" fill="none" stroke="#1f2a2a" stroke-width="2.2"><path d="M4 12h15M13 6l6 6-6 6"/></svg></span>
</a>

<section class="abs" style="left:161px;top:1147px">
  <h2 class="sec-title serif">About us</h2>
  <p class="sec-sub">Lorem Ipsum Dolor Sit Amet, Consectetur Adipiscing Elit, Sed Do Eiusmod Tempor</p>
</section>
<div class="about-box abs"></div>
<div class="about-text abs">
  <p>Lorem Ipsum Dolor Sit Amet, Consectetur Adipiscing Elit, Sed Do Eiusmod Tempor Incididunt Ut Labore Et Dolore Magna Aliqua. Ut Enim Ad Minim Veniam, Quis Nostrud Exercitation Ullamco Laboris Nisi Ut Aliquip Ex Ea Commodo Consequat. Duis Aute Irure Dolor In Reprehenderit In Voluptate Velit Esse Cillum Dolore Eu Fugiat Nulla Pariatur. Excepteur Sint Occaecat Cupidatat Non Proident, Sunt In Culpa Qui Officia Deserunt Mollit Anim Id Est Laborum. Duis Aute Irure Dolor In Reprehenderit In Voluptate Velit Esse Cillum Dolore Eu Fugiat Nulla Pariatur. Excepteur Sint Occaecat Cupidatat Non Proident, Sunt In Culpa Qui Officia.A Pariatur. Excepteur Sint Occaecat Cupidatat Non Proident, Sunt In Culpa Qui Officia.</p>
  <span class="btn btn-light">Read More</span>
</div>
<div class="about-photo abs" role="img" aria-label="Four friends posing together on a seaside pier"></div>

<section class="abs" style="left:161px;top:1670px">
  <h2 class="sec-title serif">You might like these Activities</h2>
  <p class="sec-sub">More Things To Do In Brimwell Park</p>
</section>

<div class="act-card abs" style="left:161px;top:1748px">
  <div class="img" role="img" aria-label="Costumed character on a stage" style="background:linear-gradient(160deg,#7d7fb5,#4a4b6e 55%,#2a2a36)"></div>
  <div class="row"><span>Fairy Tale Castle Tours</span><span class="score">★ 5.0</span></div>
  <div class="desc">Points Of Inatrest &amp; Land Marks...</div>
</div>
<div class="act-card abs" style="left:388px;top:1748px">
  <div class="img" role="img" aria-label="Fireworks bursting over a castle at night" style="background:linear-gradient(180deg,#1a0d1c,#6a1c3d 55%,#4b2a78)">
    <span class="heart"><svg width="14" height="14" viewBox="0 0 24 24" fill="none" stroke="#1f2a2a" stroke-width="2"><path d="M12 20s-7-4.4-7-10a4 4 0 0 1 7-2.6A4 4 0 0 1 19 10c0 5.6-7 10-7 10z"/></svg></span>
  </div>
  <div class="row"><span>Fireworks Shows</span><span class="score">★ 5.0</span></div>
  <div class="desc">Points Of Inatrest &amp; Land Marks...</div>
</div>
<div class="act-card abs" style="left:614px;top:1748px">
  <div class="img" role="img" aria-label="Balloon seller in front of a decorated street café" style="background:linear-gradient(180deg,#a85a4a,#c9b7c8 55%,#6b5a55)">
    <span class="heart"><svg width="14" height="14" viewBox="0 0 24 24" fill="none" stroke="#1f2a2a" stroke-width="2"><path d="M12 20s-7-4.4-7-10a4 4 0 0 1 7-2.6A4 4 0 0 1 19 10c0 5.6-7 10-7 10z"/></svg></span>
  </div>
  <div class="row"><span>Themed Cafés</span><span class="score">★ 5.0</span></div>
  <div class="desc">Points Of Inatrest &amp; Land Marks...</div>
</div>
<div class="act-card abs" style="left:841px;top:1748px">
  <div class="img" role="img" aria-label="Costumed performers riding a parade float among trees" style="background:linear-gradient(160deg,#5d7a5a,#8a9a7a 50%,#b08a6a)">
    <span class="heart"><svg width="14" height="14" viewBox="0 0 24 24" fill="none" stroke="#1f2a2a" stroke-width="2"><path d="M12 20s-7-4.4-7-10a4 4 0 0 1 7-2.6A4 4 0 0 1 19 10c0 5.6-7 10-7 10z"/></svg></span>
  </div>
  <div class="row"><span>Character Experiences</span><span class="score">★ 5.0</span></div>
  <div class="desc">Points Of Inatrest &amp; Land Marks...</div>
</div>
<span class="carousel-next abs"><svg width="14" height="14" viewBox="0 0 24 24" fill="none" stroke="#1f2a2a" stroke-width="2.2"><path d="M4 12h15M13 6l6 6-6 6"/></svg></span>

<article class="post abs" style="top:2065px">
  <div class="thumb" role="img" aria-label="Straight desert highway toward red rock buttes" style="background:linear-gradient(180deg,#c9b9a8,#a8684a 55%,#6e3c2a)"></div>
  <div class="body">
    <span class="tag">Texas Road Tips</span>
    <h3 class="serif">Seven Perfect days in Texas</h3>
    <p>Lorem Ipsum Dolor Sit Amet, Consectetur Adipiscing Elit, Sed Do Eiusmod Tempor Incididunt Ut Labore Et Dolore Magna Aliqua. Ut Enim Ad Minim Veniam, Quis Nostrud Exercitation.</p>
  </div>
  <span class="btn btn-outline">Read Now</span>
</article>
<article class="post abs" style="top:2217px">
  <div class="thumb" role="img" aria-label="Palm-lined beach boulevard with parked cars" style="background:linear-gradient(180deg,#4d8fd0,#8fb6d6 55%,#6a6058)"></div>
  <div class="body">
    <span class="tag">Florida Beaches</span>
    <h3 class="serif">Top 10 offbeat beaches in Florida</h3>
    <p>Lorem Ipsum Dolor Sit Amet, Consectetur Adipiscing Elit, Sed Do Eiusmod Tempor Incididunt Ut Labore Et Dolore Magna Aliqua. Ut Enim Ad Minim Veniam, Quis Nostrud Exercitation.</p>
  </div>
  <span class="btn btn-outline">Read Now</span>
</article>

<section class="contact abs">
  <div class="contact-info">
    <div class="item">
      <svg width="26" height="26" viewBox="0 0 24 24" fill="none" stroke="#fff" stroke-width="1.5"><path d="M12 21s-7-6.2-7-11.5a7 7 0 0 1 14 0C19 14.8 12 21 12 21z"/><circle cx="12" cy="9.5" r="2.5"/></svg>
      <h4>Address</h4>
      <p>48 Larkspur Lane<br>Millbrook, Oregon</p>
    </div>
    <div class="item">
      <svg width="24" height="24" viewBox="0 0 24 24" fill="none" stroke="#fff" stroke-width="1.5"><path d="M5 3h4l2 5-2.5 1.5a11 11 0 0 0 6 6L16 13l5 2v4a2 2 0 0 1-2 2A17 17 0 0 1 3 5a2 2 0 0 1 2-2z"/></svg>
      <h4>Phone</h4>
      <p>+1 555-014-2267<br>+1 555-019-3381</p>
    </div>
    <div class="item">
      <svg width="26" height="22" viewBox="0 0 24 20" fill="none" stroke="#fff" stroke-width="1.5"><rect x="2" y="3" width="20" height="14"/><path d="M2 3l10 8 10-8M2 17l7-7M22 17l-7-7"/></svg>
      <h4>Email</h4>
      <p><a>hello@roamwell</a><br><a>travel.com</a></p>
    </div>
  </div>
  <div class="contact-divider"></div>
  <div class="contact-form">
    <h2 class="serif">Send Us A Message</h2>
    <p>Lorem Ipsum Dolor Sit Amet, Consectetur Adipiscing Elit, Sed Do Eiusmod Tempor Incididunt Ut Labore Et Dolore Magna Aliqua. Ut Enim Ad Minim Veniam, Quis Nostrud Exercitation.</p>
    <div class="field">Enter your name</div>
    <div class="field">Enter your email</div>
    <div class="field tall">Enter your message</div>
    <span class="btn btn-light">Send Now</span>
  </div>
</section>

<section class="promo abs">
  <div class="promo-copy">
    <h2 class="serif">We Are Best Of The Best</h2>
    <p>Join our community and be the first to receive exclusive offers, expert skincare tips, and early access to exciting new product launches—delivered straight to your inbox.</p>
    <span class="btn btn-outline">Book your trip</span>
  </div>
  <svg class="promo-collage" viewBox="0 0 420 360" role="img" aria-label="Collage of tropical coastlines, islands and beach resorts in diagonal frames">
    <defs>
      <linearGradient id="sea1" x1="0" y1="0" x2="1" y2="1"><stop offset="0" stop-color="#5e8a6a"/><stop offset="1" stop-color="#5fb3bf"/></linearGradient>
      <linearGradient id="sea2" x1="0" y1="0" x2="1" y2="1"><stop offset="0" stop-color="#7cc4cc"/><stop offset="1" stop-color="#2f6f80"/></linearGradient>
      <linearGradient id="sea3" x1="0" y1="0" x2="0" y2="1"><stop offset="0" stop-color="#8fc7e0"/><stop offset="1" stop-color="#3f8a83"/></linearGradient>
    </defs>
    <g transform="rotate(35 210 180)">
      <rect x="150" y="-30" width="110" height="120" rx="55" fill="url(#sea3)"/>
      <rect x="90" y="110" width="110" height="260" rx="55" fill="url(#sea1)"/>
      <rect x="220" y="50" width="110" height="200" rx="55" fill="url(#sea2)"/>
      <rect x="230" y="270" width="110" height="140" rx="55" fill="url(#sea3)"/>
    </g>
  </svg>
</section>

<footer class="site-footer abs">
  <div class="nl-eyebrow abs">
    <svg width="16" height="12" viewBox="0 0 24 18" fill="none" stroke="#e5efee" stroke-width="1.6"><rect x="2" y="2" width="20" height="14"/><path d="M2 2l10 8 10-8"/></svg>
    Signup for our emails
  </div>
  <h2 class="nl-title serif abs">Subscribe To Our Newsletter</h2>
  <span class="nl-label abs" style="left:190px">Email Address <span style="color:#e88">*</span></span>
  <span class="nl-label abs" style="left:466px">Area Of Interest</span>
  <div class="nl-input abs" style="left:190px">Enter your email address</div>
  <div class="nl-input abs" style="left:466px">Make a selection <span>⌄</span></div>
  <span class="btn btn-light nl-btn abs">Subscribe</span>
  <p class="nl-note abs">*By Proceding You Agree To Our <u>Terms &amp; Policy</u> And <u>Cookie Statement</u> And <u>Term Of Use</u></p>

  <div class="f-rule abs" style="top:301px"></div>

  <div class="f-brand abs"><span class="mark"></span>Roamwell Travel</div>

  <div class="f-col abs" style="left:363px">
    <h5>Explore</h5>
    What We Offer<br>Blog &amp; Insights<br>Resources<br>FAQs
  </div>
  <div class="f-col abs" style="left:520px">
    <h5>Company</h5>
    Home<br>About Us<br>Contact Us<br>Testimonials
  </div>
  <div class="f-col abs" style="left:678px">
    <h5>Legal Links</h5>
    Privacy Policy<br>Cookie Policy<br>Disclaimer<br>Copyright
  </div>
  <div class="f-col abs" style="left:835px"><h5>Social</h5></div>
  <div class="socials abs"><span><i></i></span><span><i></i></span><span><i></i></span><span><i></i></span></div>

  <div class="f-rule abs" style="top:486px"></div>
  <p class="copyright abs">Copyright © 2025 Roamwell Travel. All Rights Reserved.</p>
  <div class="legal abs"><span>Teams &amp; Conditions</span><span>Privacy Policy</span></div>
</footer>

</body>
</html>
```